ULMIRA card Technical Architecture

Hello everyone ULMIRA: It is a consulting firm in Architecture and Construction. I require a card duplexing, sober, elegant, classic but not boring. Update 1: Use the following data for the card. Name: Gonzalo Pereda Mauricio Villalta Position: COO Twitter: @ulmiraAT Homepage: ulmira-example.com home address not include the participation of all thank you.

Target Market(s)

Construction companies, Architects and Consulting Engineers

Industry/Entity Type

Consulting

Contact Information for Business Card

Los campos que debe tener:
Nombre, Cargo, email, homepage y twitter

Font styles to use
Serif
Sans Serif
Other font styles liked:
• Me gustan playfair display, open sans y roboto, pero estoy sujeto a sus propuestas

Requirements
Must have
• Colors: Present combined proposals in white, red, gray and black Update 1: The two names must be clearly differentiated from the two surnames
Nice to have
• They are free to present their best proposals. I will bring them immediate feedback to the extent you can go see their designs. Complete data for card and logo files will give the winner the

```html
<!DOCTYPE html>
<html lang="es">
<head>
<meta charset="utf-8">
<title>ULMIRA business card</title>
<link href="https://fonts.googleapis.com/css2?family=Roboto:wght@300;400;500&display=swap" rel="stylesheet">
<style>
  :root{
    --stage:#3f3834;
    --card:#141516;
    --card-edge:#1d1e20;
    --ink-white:#f2f2f2;
    --ink-gray:#8a8b8d;
    --ink-dim:#3a3b3d;
    --accent-red:#b3121c;
    --rule:#6d6e70;
  }
  *{box-sizing:border-box;margin:0;padding:0}
  html,body{width:1200px;height:864px;overflow:hidden}
  body{background:var(--stage);font-family:"Roboto",Arial,sans-serif;position:relative}
  .card{
    position:absolute;top:282px;width:520px;height:297px;
    background:linear-gradient(160deg,var(--card-edge),var(--card));
    border-radius:3px;box-shadow:0 10px 28px rgba(0,0,0,.45);
  }
  .card--back{left:50px}
  .card--front{left:630px}

  /* back side */
  .back-brand{
    position:absolute;left:0;right:0;top:105px;text-align:center;
    font-weight:400;font-size:40px;letter-spacing:12px;color:var(--ink-dim);
  }
  .back-url{
    position:absolute;left:0;right:0;top:190px;text-align:center;
    font-weight:300;font-size:13px;letter-spacing:5px;color:var(--ink-gray);
  }

  /* front side */
  .front-brand{
    position:absolute;left:190px;top:88px;
    display:flex;align-items:center;gap:12px;
  }
  .front-brand__square{width:14px;height:14px;background:var(--accent-red)}
  .front-brand__name{
    font-weight:400;font-size:30px;letter-spacing:9px;color:var(--ink-white);
  }
  .front-brand__rule{
    position:absolute;left:190px;top:136px;width:270px;height:1px;background:var(--rule);
  }
  .person{
    position:absolute;right:292px;top:176px;text-align:right;
  }
  .person__name{font-size:16px;color:var(--accent-red);font-weight:400}
  .person__role{font-size:15px;color:var(--ink-white);font-weight:300;margin-top:3px}
  .divider{position:absolute;left:238px;top:170px;width:1px;height:74px;background:var(--rule)}
  .contacts{position:absolute;left:254px;top:176px;list-style:none}
  .contacts li{
    display:flex;align-items:center;gap:9px;
    font-size:13px;color:var(--ink-white);font-weight:300;height:21px;
  }
  .contacts svg{width:12px;height:12px;flex:none}
  .contacts .dot{width:9px;height:9px;border-radius:50%;background:var(--accent-red);margin:0 1.5px}
</style>
</head>
<body>
  <section class="card card--back" aria-label="Card back">
    <div class="back-brand">ULMIRA</div>
    <div class="back-url">www.ulmira-example.com</div>
  </section>

  <section class="card card--front" aria-label="Card front">
    <div class="front-brand">
      <span class="front-brand__square"></span>
      <span class="front-brand__name">ULMIRA</span>
    </div>
    <div class="front-brand__rule"></div>

    <div class="person">
      <div class="person__name">Tomas Rivel</div>
      <div class="person__role">President</div>
    </div>
    <div class="divider"></div>
    <ul class="contacts">
      <li>
        <svg viewBox="0 0 12 12" aria-hidden="true"><path fill="#b3121c" d="M2.5 1h2l1 3-1.3 1a6 6 0 0 0 2.8 2.8L8 6.5l3 1v2c0 .8-.7 1.5-1.5 1.5A8.5 8.5 0 0 1 1 2.5C1 1.7 1.7 1 2.5 1z"/></svg>
        555 0190 4417
      </li>
      <li>
        <svg viewBox="0 0 12 12" aria-hidden="true"><rect x="0.5" y="2" width="11" height="8" rx="1" fill="#b3121c"/><path d="M1 2.8 6 6.6 11 2.8" stroke="#141516" stroke-width="1" fill="none"/></svg>
        tomas@ulmira-example.com
      </li>
      <li>
        <span class="dot"></span>
        @ulmira
      </li>
    </ul>
  </section>
</body>
</html>
```